Travel, Resort and Tourism Advisor

I am looking for a classy and slick website for a travel, resort and tourism website which will offer first hand advise to tourist and fun seekers on the best locations and remarkable places to relax and unwind. We are primary located in the United States but will offer services to people worldwide. My website will feature images and locations and analysis of the best resorts in the Industry. Designers can take an idea from http://wandervale.example It will include prices, safety tips, culture and how to make the best of your tourism. The website will compare different destinations and recommend places based on the user budget, culture, and ethnic nationality. I would want a colorful and attention seeking website. Have questions ask.
Industry/Entity Type
Tourism
Coding
Coded - Design and coding required
Number of Pages Required
1 page
Look and feel
Each slider illustrates characteristics of the customer's brand and the style your logo design should communicate.

```html
<!DOCTYPE html>
<html lang="en">
<head>
<meta charset="utf-8">
<title>Solano Advisors — Travel &amp; Tourism Advisor</title>
<link href="https://fonts.googleapis.com/css2?family=Montserrat:wght@400;500;600;700&family=Raleway:wght@300;400;500&display=swap" rel="stylesheet">
<style>
:root{
  --brand:#1a8db4;
  --brand-dark:#0f7ca3;
  --topbar:#127fa6;
  --ink:#1d1d1d;
  --muted:#7b7b7b;
  --line:#e6e6e6;
  --red:#e9503f;
  --cyan:#2fc1d8;
  --green:#4ccb68;
  --purple:#c273de;
  --white:#ffffff;
}
*{box-sizing:border-box;margin:0;padding:0}
html,body{width:1200px;height:3209px;overflow:hidden}
body{position:relative;background:var(--white);font-family:"Raleway",Arial,sans-serif;color:var(--ink)}
.abs{position:absolute}
.heading-font{font-family:"Montserrat",Arial,sans-serif}

/* top bar */
.topbar{left:0;top:0;width:1200px;height:43px;background:var(--topbar);color:#dff1f8;font-size:12px;font-family:"Montserrat",Arial,sans-serif}
.topbar .contact{left:100px;top:14px;display:flex;gap:40px}
.topbar .contact span{display:flex;align-items:center;gap:10px}
.topbar .social{right:100px;top:16px;display:flex;gap:10px}
.dot{width:10px;height:10px;border-radius:50%;background:#dff1f8}

/* header */
.header{left:0;top:43px;width:1200px;height:111px;background:var(--white)}
.logo{left:100px;top:33px;display:flex;align-items:center;gap:12px;font-family:"Montserrat",Arial,sans-serif;font-weight:500;font-size:28px;color:var(--brand)}
.logo .mark{width:34px;height:34px;border-radius:50%;border:3px solid var(--brand)}
.nav{left:487px;top:0;height:111px;display:flex;font-family:"Montserrat",Arial,sans-serif;font-weight:600;font-size:13px;color:#222}
.nav a{display:block;padding:47px 20px 0;height:111px;text-decoration:none;color:inherit}
.nav a.active{color:var(--brand);border-bottom:3px solid var(--brand)}

/* hero */
.hero{left:0;top:154px;width:1200px;height:590px;background:linear-gradient(180deg,#8cc8d8 0%,#6fb2c6 45%,#4f8f8a 75%,#3b6f6a 100%)}
.hero-title{left:100px;top:214px;color:var(--white);font-family:"Montserrat",Arial,sans-serif}
.hero-title .small{font-size:36px;font-weight:400;letter-spacing:1px}
.hero-title .big{font-size:44px;font-weight:700;margin-top:4px;letter-spacing:.5px}
.arrow-btn{width:44px;height:44px;border-radius:50%;background:rgba(255,255,255,.25);top:418px}
.search{top:682px;height:40px;background:var(--white);display:flex;align-items:center;padding-left:12px;font-size:14px;color:#333;font-family:"Montserrat",Arial,sans-serif}
.search .ph{color:#aaa;margin-left:10px;font-family:"Raleway",Arial,sans-serif}
.search-btn{left:941px;top:682px;width:161px;height:40px;background:var(--cyan);color:var(--white);font-family:"Montserrat",Arial,sans-serif;font-weight:600;font-size:14px;display:flex;align-items:center;justify-content:center;letter-spacing:1px}

/* welcome */
.section-title{width:1200px;left:0;text-align:center;font-family:"Montserrat",Arial,sans-serif;font-weight:700;font-size:30px;color:#1d1d1d}
.section-title em{font-style:normal;color:var(--brand)}
.intro{left:139px;top:846px;width:924px;text-align:center;font-size:13px;line-height:28px;color:var(--muted)}
.rule{left:300px;top:942px;width:600px;height:1px;background:var(--line)}
.service{top:978px;width:240px;text-align:center}
.service .circle{width:124px;height:124px;border-radius:50%;margin:0 auto;display:flex;align-items:center;justify-content:center;border:6px solid #eef3f5}
.service h3{font-family:"Montserrat",Arial,sans-serif;font-weight:700;font-size:15px;margin-top:26px;letter-spacing:.5px}
.service p{font-size:13px;line-height:21px;color:var(--muted);margin:12px auto 0;width:210px}
.service .btn{display:block;width:152px;height:45px;margin:30px auto 0;border:1.5px solid;font-family:"Montserrat",Arial,sans-serif;font-size:14px;line-height:42px;letter-spacing:.5px}

/* band */
.band{left:0;top:1345px;width:1200px;height:430px;background:linear-gradient(180deg,#2b9fc8 0%,#1f8fbd 60%,#1a86b4 100%);color:var(--white);text-align:center}
.band h2{position:absolute;left:0;top:54px;width:1200px;font-family:"Raleway",Arial,sans-serif;font-weight:400;font-size:56px;letter-spacing:1px}
.band p{position:absolute;left:180px;top:140px;width:840px;font-size:23px;line-height:35px;font-weight:300;color:#e8f5fa}
.band .book{position:absolute;left:466px;top:306px;width:268px;height:51px;border:1.5px solid rgba(255,255,255,.8);font-family:"Montserrat",Arial,sans-serif;font-weight:600;font-size:18px;line-height:48px;letter-spacing:1px}

/* destinations */
.pager{top:1826px;display:flex;gap:6px}
.pager span{width:26px;height:26px;border-radius:50%;background:#e4e4e4;display:flex;align-items:center;justify-content:center}
.dest{top:1900px;width:315px}
.dest .photo{height:183px}
.dest h3{font-family:"Montserrat",Arial,sans-serif;font-weight:400;font-size:20px;margin-top:26px;letter-spacing:.5px}
.dest p{font-size:14px;line-height:21px;color:var(--muted);margin-top:12px}
.dest .btn{display:inline-flex;align-items:center;gap:8px;margin-top:40px;height:41px;padding:0 18px;color:var(--white);font-family:"Montserrat",Arial,sans-serif;font-size:14px}

/* packages */
.packages{left:0;top:2351px;width:1200px;height:539px;background:linear-gradient(180deg,#1784ad 0%,#3aa6c4 45%,#7ec7d0 70%,#4d9fa3 100%)}
.pkg{top:2477px;width:315px;background:var(--white)}
.pkg .photo{height:182px}
.pkg p{font-size:13px;line-height:21px;color:#555;text-align:center;padding:20px 24px 0;height:110px}
.pkg .meta{display:flex;justify-content:space-between;align-items:flex-end;padding:0 18px 16px 28px;border-top:1px solid #eee;padding-top:10px}
.pkg .from{font-size:9px;color:#999;letter-spacing:1px;font-family:"Montserrat",Arial,sans-serif}
.pkg .price{font-family:"Montserrat",Arial,sans-serif;font-weight:500;font-size:21px;color:#222}
.pkg .btn{height:33px;padding:0 14px;color:var(--white);font-family:"Montserrat",Arial,sans-serif;font-size:12px;line-height:33px}

/* footer */
.footer{left:0;top:2890px;width:1200px;height:319px;background:var(--brand-dark);color:#e6f4f9}
.fcol{top:45px}
.fcol h4{font-family:"Montserrat",Arial,sans-serif;font-weight:700;font-size:16px;letter-spacing:.5px;color:var(--white)}
.fcol ul{list-style:none;margin-top:18px}
.fcol li{font-size:14px;line-height:30px;display:flex;align-items:center;gap:12px}
.fsep{top:40px;width:1px;height:190px;background:rgba(255,255,255,.18)}
.fsocial{display:flex;gap:6px;margin-top:20px}
.fsocial span{width:34px;height:34px;border-radius:50%;background:var(--white);border:2px solid rgba(255,255,255,.5)}
.fline{left:100px;top:246px;width:1000px;height:1px;background:rgba(255,255,255,.35)}
.copy{left:100px;top:272px;font-size:12px}
</style>
</head>
<body>

<!-- top bar -->
<div class="abs topbar">
  <div class="abs contact">
    <span><svg width="12" height="12" viewBox="0 0 24 24"><path fill="#dff1f8" d="M6.6 10.8a15 15 0 006.6 6.6l2.2-2.2a1 1 0 011-.25 11.4 11.4 0 003.6.57 1 1 0 011 1V20a1 1 0 01-1 1A17 17 0 013 4a1 1 0 011-1h3.5a1 1 0 011 1c0 1.25.2 2.45.57 3.57a1 1 0 01-.25 1z"/></svg>Call us: &nbsp;(555) 014-2290</span>
    <span><svg width="13" height="10" viewBox="0 0 26 20"><rect x="1" y="1" width="24" height="18" fill="none" stroke="#dff1f8" stroke-width="2"/><path d="M1 1l12 10 12-10" fill="none" stroke="#dff1f8" stroke-width="2"/></svg>Email us: info@solanotrips.example</span>
  </div>
  <div class="abs social"><span class="dot"></span><span class="dot"></span><span class="dot"></span><span class="dot"></span><span class="dot"></span></div>
</div>

<!-- header -->
<header class="abs header">
  <div class="abs logo"><span class="mark"></span>Solano Advisors</div>
  <nav class="abs nav">
    <a class="active">HOME</a><a>HOTELS</a><a>PAGES</a><a>PLACES</a><a>GALLERY</a><a>BLOG</a><a>CONTACT US</a>
  </nav>
</header>

<!-- hero -->
<section class="abs hero" role="img" aria-label="Hiker with a backpack and trekking poles overlooking a misty green mountain valley"></section>
<div class="abs hero-title">
  <div class="small">WE ARE A</div>
  <div class="big">TRAVEL &amp; TOURISM ADVISOR.</div>
</div>
<div class="abs arrow-btn" style="left:16px"><svg width="44" height="44"><path d="M25 14l-8 8 8 8" fill="none" stroke="#fff" stroke-width="2"/></svg></div>
<div class="abs arrow-btn" style="left:1140px"><svg width="44" height="44"><path d="M19 14l8 8-8 8" fill="none" stroke="#fff" stroke-width="2"/></svg></div>
<div class="abs search" style="left:100px;width:390px">Find: <span class="ph">Hotels, Restaurants, Things to Do</span></div>
<div class="abs search" style="left:511px;width:409px">Destination: <span class="ph">Worldwide</span></div>
<div class="abs search-btn">SEARCH</div>

<!-- welcome -->
<h1 class="abs section-title" style="top:786px">WELCOME TO <em>SOLANO ADVISORS</em></h1>
<p class="abs intro">Sed ut perspiciatis unde omnis iste natus error sit voluptatem accusantium doloremque laudantium, totam rem aperiam, eaque ipsa quae ab illo inventore veritatis et quasi architecto beatae vitae dicta sunt explicabo. Nemo enim ipsam voluptatem quia voluptas sit aspernatur aut odit aut fugit, sed quia consequuntur magni dolores eos qui ratione voluptatem sequi nesciunt.</p>
<div class="abs rule"></div>

<div class="abs service" style="left:85px">
  <div class="circle" style="background:var(--red)"><svg width="50" height="46" viewBox="0 0 50 46"><path d="M25 44L5 24A12 12 0 0125 8a12 12 0 0120 16z" fill="#fff"/><path d="M16 27l18-8M22 22l-3-6M27 21l5 8" stroke="var(--red)" stroke-width="3" stroke-linecap="round"/></svg></div>
  <h3>FLIGHTS</h3>
  <p>Praesent vestibulum aenean nonummy endrerit mauris. Cum sociis natoque..</p>
  <span class="btn" style="color:var(--red);border-color:var(--red)">READ MORE</span>
</div>
<div class="abs service" style="left:348px">
  <div class="circle" style="background:var(--cyan)"><svg width="56" height="36" viewBox="0 0 56 36"><rect x="2" y="2" width="4" height="32" fill="none" stroke="#fff" stroke-width="3"/><rect x="10" y="12" width="10" height="8" rx="3" fill="none" stroke="#fff" stroke-width="3"/><rect x="22" y="12" width="30" height="10" fill="none" stroke="#fff" stroke-width="3"/><path d="M4 26h50v8" fill="none" stroke="#fff" stroke-width="3"/></svg></div>
  <h3>HOTELS</h3>
  <p>Praesent vestibulum aenean nonummy endrerit mauris. Cum sociis natoque..</p>
  <span class="btn" style="color:var(--cyan);border-color:var(--cyan)">READ MORE</span>
</div>
<div class="abs service" style="left:614px">
  <div class="circle" style="background:var(--green)"><svg width="52" height="40" viewBox="0 0 52 40"><path d="M10 16l5-12h22l5 12h5v16h-4v6h-8v-6H17v6H9v-6H5V16z" fill="#fff"/><rect x="16" y="8" width="20" height="8" fill="var(--green)"/><circle cx="13" cy="24" r="3" fill="var(--green)"/><circle cx="39" cy="24" r="3" fill="var(--green)"/></svg></div>
  <h3>CARS</h3>
  <p>Praesent vestibulum aenean nonummy endrerit mauris. Cum sociis natoque..</p>
  <span class="btn" style="color:var(--green);border-color:var(--green)">READ MORE</span>
</div>
<div class="abs service" style="left:877px">
  <div class="circle" style="background:var(--purple)"><svg width="44" height="52" viewBox="0 0 44 52"><circle cx="16" cy="8" r="6" fill="#fff"/><path d="M8 18h16v14h-3v18h-4V36h-2v14h-4V32H8z" fill="#fff"/><path d="M28 20a8 8 0 0114 0z" fill="#fff"/><path d="M24 22h20" stroke="#fff" stroke-width="2"/></svg></div>
  <h3>RESTAURANTS</h3>
  <p>Praesent vestibulum aenean nonummy endrerit mauris. Cum sociis natoque..</p>
  <span class="btn" style="color:var(--purple);border-color:var(--purple)">READ MORE</span>
</div>

<!-- band -->
<section class="abs band" aria-label="Faint skyline of world landmarks behind">
  <h2>We are a Travel &amp; Tourism advisor</h2>
  <p>Donec sodales sagittis magna. Sed consequat, leo eget bibendum sodales. There are many variations of passages of Lorem Ipsum available, but the majority have suffered alteration in some form, by injected humour, or randomised words which don't look even slightly believable.</p>
  <span class="book">BOOK NOW !</span>
</section>

<!-- destinations -->
<h2 class="abs section-title" style="top:1818px;font-size:28px">TOP <em>DESTINATIONS</em></h2>
<div class="abs pager" style="left:1040px">
  <span><svg width="10" height="10"><path d="M7 1L3 5l4 4" fill="none" stroke="#666" stroke-width="1.5"/></svg></span>
  <span><svg width="10" height="10"><path d="M3 1l4 4-4 4" fill="none" stroke="#666" stroke-width="1.5"/></svg></span>
</div>

<article class="abs dest" style="left:100px">
  <div class="photo" role="img" aria-label="Hiker on a snowy mountain summit under a bright blue sky" style="background:linear-gradient(180deg,#3a7fc4 0%,#8fb9dd 50%,#d9e3ea 75%,#6b7a8a 100%)"></div>
  <h3>CLARITAS EST ETIAM</h3>
  <p>The simplicity and value of a destination wedding in a beautiful setting is appealing to many couples..</p>
  <span class="btn" style="background:var(--red)">Read More <svg width="8" height="10"><path d="M2 1l4 4-4 4" fill="none" stroke="#fff" stroke-width="1.5"/></svg></span>
</article>
<article class="abs dest" style="left:443px">
  <div class="photo" role="img" aria-label="Family walking on a wooden boat deck by turquoise sea" style="background:linear-gradient(180deg,#8fcbe6 0%,#4fb2d6 45%,#b07a5a 80%,#8a5a3e 100%)"></div>
  <h3>EODEM MODO</h3>
  <p>Your honeymoon should be relaxing, fun, romantic and memorable. We will assist and guide you in finding..</p>
  <span class="btn" style="background:var(--cyan)">Read More <svg width="8" height="10"><path d="M2 1l4 4-4 4" fill="none" stroke="#fff" stroke-width="1.5"/></svg></span>
</article>
<article class="abs dest" style="left:787px">
  <div class="photo" role="img" aria-label="Two people riding an inflatable tube over blue water" style="background:linear-gradient(180deg,#2a6fa8 0%,#4a93c4 50%,#d8c84a 70%,#2f77b0 100%)"></div>
  <h3>UT WISI ENIM</h3>
  <p>Family, friends, couples or whomever you care to getaway with; our team are experts in a multitude of destinations..</p>
  <span class="btn" style="background:var(--green)">Read More <svg width="8" height="10"><path d="M2 1l4 4-4 4" fill="none" stroke="#fff" stroke-width="1.5"/></svg></span>
</article>

<!-- packages -->
<section class="abs packages" role="img" aria-label="Tropical bay with green hills and clear turquoise water"></section>
<h2 class="abs section-title" style="top:2395px;font-size:28px;color:var(--white)">TOP TOUR PACKAGES</h2>

<article class="abs pkg" style="left:100px">
  <div class="photo" role="img" aria-label="Park with a tall stone monument and green lawns" style="background:linear-gradient(180deg,#4f93d8 0%,#a9cdeb 45%,#6aa84a 70%,#4a8a36 100%)"></div>
  <p>Nunc commodo ipsum in diam pulvinar, laoreet tempor tellus molestie. Maecenas blandit sem turpis, nec luctus nunc...</p>
  <div class="meta"><div><div class="from">STARTS FROM</div><div class="price">$250</div></div><span class="btn" style="background:var(--red)">VIEW DETAILS</span></div>
</article>
<article class="abs pkg" style="left:443px">
  <div class="photo" role="img" aria-label="Icebergs and snowy mountains on a deep blue sea" style="background:linear-gradient(180deg,#0f3f7a 0%,#2d6db0 40%,#dfe9f2 62%,#1a4f8f 100%)"></div>
  <p>Nunc commodo ipsum in diam pulvinar, laoreet tempor tellus molestie. Maecenas blandit sem turpis, nec luctus nunc...</p>
  <div class="meta"><div><div class="from">STARTS FROM</div><div class="price">$120</div></div><span class="btn" style="background:var(--cyan)">VIEW DETAILS</span></div>
</article>
<article class="abs pkg" style="left:787px">
  <div class="photo" role="img" aria-label="Coastal cliffs above a calm dark blue sea" style="background:linear-gradient(180deg,#0d2f6a 0%,#3f78b8 40%,#b9c3b0 58%,#1c4f8a 100%)"></div>
  <p>Nunc commodo ipsum in diam pulvinar, laoreet tempor tellus molestie. Maecenas blandit sem turpis, nec luctus nunc...</p>
  <div class="meta"><div><div class="from">STARTS FROM</div><div class="price">$150</div></div><span class="btn" style="background:var(--green)">VIEW DETAILS</span></div>
</article>

<!-- footer -->
<footer class="abs footer">
  <div class="abs fcol" style="left:100px"><h4>COMPANY</h4><ul><li>Home</li><li>About Us</li><li>Blog</li><li>News</li><li>Travels</li></ul></div>
  <div class="abs fsep" style="left:232px"></div>
  <div class="abs fcol" style="left:276px"><h4>SERVICES</h4><ul><li>Flights</li><li>Hotels</li><li>Cars</li><li>Restaurants</li><li>Others</li></ul></div>
  <div class="abs fsep" style="left:460px"></div>
  <div class="abs fcol" style="left:498px"><h4>GET IN TOUCH</h4><ul>
    <li><svg width="13" height="13" viewBox="0 0 24 24"><path fill="#e6f4f9" d="M6.6 10.8a15 15 0 006.6 6.6l2.2-2.2a1 1 0 011-.25 11.4 11.4 0 003.6.57 1 1 0 011 1V20a1 1 0 01-1 1A17 17 0 013 4a1 1 0 011-1h3.5a1 1 0 011 1c0 1.25.2 2.45.57 3.57a1 1 0 01-.25 1z"/></svg>Call us on (01) 55501234</li>
    <li><svg width="14" height="11" viewBox="0 0 26 20"><rect width="26" height="20" fill="#e6f4f9"/><path d="M0 0l13 11L26 0" fill="none" stroke="#0f7ca3" stroke-width="2"/></svg>info@solanotrips.example</li></ul></div>
  <div class="abs fsep" style="left:733px"></div>
  <div class="abs fcol" style="left:768px"><h4>WHY US</h4><ul><li>Customers</li><li>Team</li><li>FAQ</li><li>Contact</li></ul></div>
  <div class="abs fsep" style="left:887px"></div>
  <div class="abs fcol" style="left:926px"><h4>FOLLLOW US</h4><ul><li>Please connect with us on</li></ul>
    <div class="fsocial"><span style="background:#55acee"></span><span style="background:#3b5998"></span><span style="background:#0e76a8"></span><span style="background:#dd4b39"></span></div></div>
  <div class="abs fline"></div>
  <div class="abs copy">© 2016 Company Name &nbsp;All right reserved &nbsp;Term of Use</div>
</footer>

</body>
</html>
```